Wordpress Website for Trauma Ward Harm Recovery Outreach Scheme

We are looking for a wordpress website that is clean, crisp and bold for our Trauma Ward Harm Recovery Outreach Scheme.

We are a Canadian hospital in Winnipeg, MB which sees many youth injured by violence. We are starting up an Trauma Ward Harm Recovery Outreach Scheme for youth injured by violence. The youth who we will serve will be between the age of 14 - 24 and many will be gang-involved.

However, it is important to note that this website isn't for the youth themselves as much as it is for professionals and community interested in learning about our program. As such, it is should be friendly but professional. I am interested in a bold, crisp look.

I have attached our logo file for your use.
Updates

I forgot to mention that there should be a section along the bottom to include logos of funders and partners.

Also would be nice to include a spot for viewers to automatically subscribe to our newsletter by putting their email in.

I have added in a file of text that I will use - but want to easily be able to change and update (and post links etc). 

Target Market(s)

This will target a professional and community audience. We would like a crisp, bold, professional presence

Industry/Entity Type

Hospital

Requirements
Must have
• I would like a navigation bar that includes the following:

About TW-ROS (Background and Research sections)
People
Latest News
Job Opportunities
Research Opportunities
Publications & Reports
Contact TW-ROS ( a form)

I would also like a search form and a link to twitter.

While I am comfortable with Wordpress - I am not an expert. I want this to be as simple as possible for me to update.
Nice to have
• We have a great logo and only a few photos which I will upload in the next day.

We could also use stock photos for now but overtime switch these with photos of our own hospital emergency department and team. Additionally, we would like some stock photos of youth - a diverse mix but to include Aboriginal/First Nations, immigrant and caucasian youth
Should not have
• This design should not have guns, knifes, alcohol or blood/gore in there (I've learned to state this after using pixel throng for the logo! )

```html
<!DOCTYPE html>
<html lang="en">
<head>
<meta charset="utf-8">
<title>TW-ROS – Trauma Ward Harm Recovery Outreach Scheme</title>
<link rel="stylesheet" href="https://fonts.googleapis.com/css2?family=Ubuntu:wght@400;500;700&family=Arimo:wght@400;700&family=PT+Sans:wght@400&display=swap">
<style>
:root{
  --red:#a01f2b;
  --red-dark:#7d1620;
  --red-light:#c02a36;
  --text:#555;
  --heading:#222;
  --rule:#d6d6d6;
  --frame:#ebe5e6;
  --footer:#232323;
}
html,body{margin:0;padding:0;width:1108px;height:1200px;overflow:hidden;background:#fff}
.page{position:relative;width:1200px;height:1300px;transform:scale(0.92333);transform-origin:0 0;font-family:"Arimo",Arial,sans-serif;color:var(--text)}
.top-band{position:absolute;left:0;top:0;width:1200px;height:612px;background:repeating-linear-gradient(135deg,#f2f2f2 0 2px,#ebebeb 2px 4px);border-bottom:1px solid #ddd}
.brand{position:absolute;left:120px;top:32px;height:70px;display:flex;align-items:center;gap:14px}
.brand-name{font-family:"Ubuntu",sans-serif;font-weight:700;font-size:34px;color:var(--red);letter-spacing:1px}
.brand-tagline{font-family:"Ubuntu",sans-serif;font-size:12px;line-height:13.5px;color:#666;width:110px}
.search{position:absolute;left:829px;top:42px;width:250px;height:35px;background:#f7f7f7;border:1px solid #ddd;border-radius:3px}
.search-divider{position:absolute;left:212px;top:8px;width:1px;height:20px;background:#ccc}
.search svg{position:absolute;left:222px;top:10px}
.main-nav{position:absolute;left:120px;top:120px;width:960px;height:47px;box-sizing:border-box;padding:0 16px 0 0;margin:0;list-style:none;background:linear-gradient(#bd2633,#951b25);display:flex;align-items:stretch;justify-content:space-between}
.main-nav li{font-family:"Ubuntu",sans-serif;font-weight:500;font-size:13px;color:#fff;display:flex;align-items:center;white-space:nowrap;letter-spacing:.2px}
.main-nav li.active{background:linear-gradient(#fdfdfd,#e3e3e3);color:var(--red);width:72px;justify-content:center}
.slider{position:absolute;left:120px;top:186px;width:958px;height:378px;background:var(--frame);border:1px solid #ddd;box-shadow:0 18px 16px -14px rgba(0,0,0,.25)}
.slide{position:absolute;left:10px;top:10px;width:938px;height:358px;background:linear-gradient(120deg,#8a8a8a,#c9c2bd 45%,#3e3c3e 80%,#2a2a2e)}
.dots{position:absolute;left:572px;top:589px;display:flex;gap:5px}
.dots span{width:10px;height:10px;border-radius:50%;background:#bbb;box-shadow:inset 0 1px 2px rgba(0,0,0,.4)}
.dots span.on{background:#666}
.section{position:absolute}
.section h2{margin:0;font-family:"Ubuntu",sans-serif;font-weight:500;font-size:21px;color:var(--heading);height:26px}
.section h2 em{font-style:normal;color:var(--red)}
.section .rule{height:2px;background:var(--rule);margin-top:13px}
.section p{margin:0;font-size:12px;line-height:18px;text-align:justify}
.btn{position:absolute;width:60px;height:30px;background:linear-gradient(var(--red-light),var(--red-dark));color:#fff;font-family:"Ubuntu",sans-serif;font-weight:700;font-size:14px;display:flex;align-items:center;justify-content:center;border-radius:2px}
.photo{position:absolute}
.subhead{font-size:13px;color:var(--red);margin:0}
.divider{position:absolute;left:120px;top:896px;width:960px;height:2px;background:#e2e2e2}
.job p{text-align:left;line-height:20px}
.job a{color:var(--red);font-weight:bold;text-decoration:none}
.footer{position:absolute;left:0;top:1242px;width:1200px;height:58px;background:var(--footer);border-top:1px solid #555}
.footer .copy{position:absolute;left:120px;top:18px;font-family:"PT Sans",sans-serif;font-size:13px;color:#eee}
.social{position:absolute;left:860px;top:8px;display:flex;gap:7px}
.social span{width:38px;height:38px;border-radius:50%;background:#9d4650;box-shadow:inset 0 0 0 2px #b5606a}
.footer .code{position:absolute;left:1152px;top:18px;font-family:"PT Sans",sans-serif;font-size:13px;color:#ddd}
</style>
</head>
<body>
<div class="page">
  <div class="top-band"></div>

  <header class="brand">
    <span class="brand-name">TW-ROS</span>
    <span class="brand-tagline">Trauma Ward Harm Recovery Outreach Scheme</span>
  </header>

  <div class="search" role="search">
    <span class="search-divider"></span>
    <svg width="14" height="14" viewBox="0 0 14 14"><circle cx="5" cy="5" r="3.5" fill="none" stroke="#777" stroke-width="1.6"/><line x1="7.5" y1="7.5" x2="12" y2="12" stroke="#777" stroke-width="2"/></svg>
  </div>

  <ul class="main-nav">
    <li class="active">HOME</li>
    <li>ABOUT</li>
    <li>PEOPLE</li>
    <li>LATEST NEWS</li>
    <li>JOB OPPORTUNITIES</li>
    <li>RESEARCH OPPORTUNITIES</li>
    <li>PUBLICATIONS &amp; REPORTS</li>
    <li>CONTACT</li>
  </ul>

  <div class="slider">
    <div class="slide" role="img" aria-label="Group of professionals in business attire meeting and exchanging cards"></div>
  </div>
  <div class="dots"><span></span><span class="on"></span><span></span><span></span></div>

  <section class="section" style="left:120px;top:626px;width:630px">
    <h2>&nbsp;Welcome to <em>TWROS!</em></h2>
    <div class="rule"></div>
  </section>
  <div class="photo" role="img" aria-label="Counsellor speaking with a young woman on a sofa" style="left:120px;top:678px;width:250px;height:155px;background:linear-gradient(90deg,#d9cbb2,#b9a88c 50%,#6e5540 80%,#3fb3ad)"></div>
  <div class="section" style="left:378px;top:675px;width:372px">
    <p>Youth injured by violence is a concerning issue in Canada. Youth homicide is the fourth most common reason of death among youth in Canada and in some provinces, the most common reason for visiting an emergency department.</p>
    <p style="margin-top:18px">Even more concerning is that there is a high repeat rate of visits to emergency departments for subsequent injuries caused by violence. At the Riverbend Health Sciences Centre, 20% of youth injured by violence return for a subsequent injury within the next year.</p>
  </div>
  <span class="btn" style="left:120px;top:846px">MORE</span>

  <section class="section" style="left:780px;top:626px;width:300px">
    <h2>Latest News</h2>
    <div class="rule"></div>
    <p style="margin-top:11px;height:162px;overflow:hidden">In June 2013, the youth violence research program at Prairie Institute of Child Health, Northfield University was awarded two operating grants to support the study “WrapAround Care for Youth Injured by Violence: A Pilot Randomized Control Trial.”<br><br>These operating grants were received from the National Council for Health Research and Prairie Institute of Child Health. We are excited and appreciative of these</p>
  </section>
  <span class="btn" style="left:780px;top:846px">MORE</span>

  <div class="divider"></div>

  <section class="section" style="left:120px;top:922px;width:300px">
    <h2>Our <em>People</em></h2>
    <div class="rule"></div>
  </section>
  <div class="photo" role="img" aria-label="Portrait of the principal investigator" style="left:120px;top:967px;width:298px;height:127px;border:1px solid #ddd;background:linear-gradient(90deg,#fff 25%,#c9a48a 45%,#e6d3c5 60%,#fff 75%)"></div>
  <div class="section" style="left:120px;top:1107px;width:300px">
    <p class="subhead">Principal Investigator</p>
    <p>Dr. Helen Marsh, is an emergency physician and researcher in youth violence in Riverbend, Manitoba. Dr. Marsh graduated from Lakeside Medical School..</p>
  </div>
  <span class="btn" style="left:120px;top:1190px">MORE</span>

  <section class="section" style="left:450px;top:922px;width:300px">
    <h2>Research <em>Opportunities</em></h2>
    <div class="rule"></div>
  </section>
  <div class="photo" role="img" aria-label="Doctors and nurses in a bright hospital ward" style="left:450px;top:967px;width:298px;height:127px;border:1px solid #ddd;background:linear-gradient(90deg,#e9eef3,#d9dfe6 40%,#b9c6d3 70%,#4aa0b8)"></div>
  <div class="section" style="left:450px;top:1106px;width:299px">
    <p>Please contact Dr. Marsh at hmarsh@wardmail.ca if you are interested in research with the TW-ROS. Dr. Marsh is currently accepting students interested in Graduate, BSc Med and undergraduate summer student positions.</p>
  </div>
  <span class="btn" style="left:450px;top:1190px">MORE</span>

  <section class="section job" style="left:780px;top:922px;width:300px">
    <h2>job <em>Opportunities</em></h2>
    <div class="rule"></div>
    <p class="subhead" style="margin-top:8px;line-height:18px">A) SOCIAL WORKERS</p>
    <p>Anticipated Number of Positions Available:<br>1 Full-Time: 35 hours/week<br>1 Part-Time: 21 hours/week<br><br>Anticipated Position Start date: October 21<br>To apply for this position please <a href="#">click here</a><br><br>(Please note: This job is listed as a Northfield University Office Assistant 3 classification)</p>
  </section>
  <span class="btn" style="left:780px;top:1190px">MORE</span>

  <footer class="footer">
    <span class="copy">Copyright 2013 TWROS | Al Rights Reserved.</span>
    <div class="social" aria-label="Social links"><span></span><span></span><span></span><span></span><span></span></div>
    <span class="code">C2</span>
  </footer>
</div>
</body>
</html>
```